SOLVE Study flyer

I need help designing a flyer for a research study that will include brain imaging in adolescents. The info is in the attached document. The study is called the Sequoia Outlook Lantern Valley Echo (SOLVE) study. Ideally this would be returned as a document that I can edit in the future as we will have several new recruitment phases (different age groups, etc. I also would love to have a logo designed as part of this project, but I recognize that might be a separate design request.

```html
<!DOCTYPE html>
<html lang="en">
<head>
<meta charset="utf-8">
<title>SOLVE Study Flyer</title>
<link href="https://fonts.googleapis.com/css2?family=Poppins:wght@300;400;500;600;700;800&display=swap" rel="stylesheet">
<style>
  :root {
    --navy: #2f2a6e;
    --purple: #7a4fc8;
    --violet: #a98ae0;
    --lavender: #eeecf6;
    --lavender-deep: #dcd7ee;
    --yellow: #f4c23c;
    --ink: #3b3a4a;
    --paper: #ffffff;
    --backdrop: #dcdcdc;
  }
  * { box-sizing: border-box; margin: 0; padding: 0; }
  html, body { width: 1200px; height: 900px; overflow: hidden; }
  body {
    background: var(--backdrop);
    font-family: "Poppins", sans-serif;
    color: var(--ink);
    position: relative;
  }
  .flyer {
    position: absolute; left: 270px; top: 20px;
    width: 660px; height: 860px;
    background: var(--paper);
    overflow: hidden;
    box-shadow: 0 6px 24px rgba(0,0,0,.12);
  }
  .hero-photo { position: absolute; right: 0; top: 0; width: 300px; height: 340px; }

  .brand { position: absolute; left: 40px; top: 62px; display: flex; align-items: center; gap: 14px; }
  .brand-dot { width: 64px; height: 64px; border-radius: 50%; background: var(--violet); }
  .brand-name { font-size: 50px; font-weight: 400; color: var(--navy); letter-spacing: 1px; line-height: 1; }
  .brand-tagline {
    position: absolute; left: 118px; top: 122px; width: 210px;
    font-size: 9.5px; letter-spacing: 1.2px; text-transform: uppercase; color: var(--navy);
    line-height: 1.35; padding-bottom: 6px; border-bottom: 2px solid var(--yellow);
  }

  .lead { position: absolute; left: 40px; top: 180px; width: 310px; }
  .headline { font-weight: 800; font-size: 21px; line-height: 1.22; }
  .headline .ask { color: var(--navy); display: block; }
  .headline .worry { color: var(--purple); display: block; }
  .headline-rule { display: block; width: 40px; height: 3px; background: var(--yellow); margin: 12px 0 10px; }
  .intro { font-size: 10.5px; line-height: 1.55; width: 290px; }
  .intro strong { color: var(--purple); font-weight: 600; }

  .card { position: absolute; background: var(--lavender); border-radius: 18px; }
  .card-title { font-size: 11px; font-weight: 700; letter-spacing: .8px; text-transform: uppercase; color: var(--purple); }
  .card-badge {
    position: absolute; width: 38px; height: 38px; border-radius: 50%;
    background: var(--paper); border: 2px solid var(--navy);
    display: flex; align-items: center; justify-content: center;
  }

  .participation { left: 40px; top: 432px; width: 300px; padding: 18px 18px 14px 64px; }
  .participation .card-badge { left: -8px; top: 8px; }
  .step { display: flex; gap: 12px; align-items: flex-start; margin-top: 12px; }
  .step-icon { flex: none; width: 38px; height: 38px; border-radius: 50%; background: var(--violet); display: flex; align-items: center; justify-content: center; margin-left: -50px; }
  .step-body { font-size: 9.5px; line-height: 1.4; padding-bottom: 8px; border-bottom: 1px solid var(--lavender-deep); flex: 1; }
  .step:last-child .step-body { border-bottom: 0; padding-bottom: 0; }
  .step-body b { display: block; font-size: 11.5px; color: var(--purple); font-weight: 700; }

  .eligibility { left: 360px; top: 362px; width: 266px; padding: 16px 20px 6px 44px; }
  .eligibility .card-badge { left: -14px; top: 100px; background: var(--navy); }
  .criteria { list-style: none; margin-top: 14px; }
  .criteria li { display: flex; gap: 10px; align-items: center; font-size: 10.5px; line-height: 1.35; margin-bottom: 16px; }
  .criteria li svg { flex: none; }
  .criteria .age { font-size: 22px; font-weight: 800; color: var(--purple); line-height: 1; display: block; }
  .criteria em { font-style: normal; color: var(--purple); font-weight: 600; }

  .contact-band { position: absolute; left: 0; top: 700px; width: 660px; height: 112px; background: var(--navy); display: flex; align-items: center; padding: 0 30px; }
  .band-icon { width: 56px; height: 56px; border-radius: 50%; background: var(--violet); display: flex; align-items: center; justify-content: center; flex: none; }
  .enquiry { margin-left: 16px; color: #fff; font-size: 10.5px; line-height: 1.35; width: 200px; }
  .enquiry .prompt { color: var(--yellow); font-weight: 700; font-size: 12px; letter-spacing: .4px; text-transform: uppercase; }
  .email-pill { display: inline-block; margin-top: 6px; background: var(--yellow); color: var(--navy); font-weight: 700; font-size: 11.5px; padding: 4px 14px; border-radius: 20px; white-space: nowrap; }
  .band-divider { width: 1px; height: 70px; background: rgba(255,255,255,.3); margin: 0 22px 0 34px; flex: none; }
  .payment { display: flex; align-items: center; gap: 14px; color: #fff; }
  .payment-label { font-size: 10px; font-weight: 600; letter-spacing: .6px; text-transform: uppercase; color: var(--yellow); line-height: 1.2; }
  .payment-label small { display: block; color: #fff; font-size: 8.5px; font-weight: 400; }
  .payment-amount { font-size: 40px; font-weight: 800; color: var(--yellow); line-height: 1; }

  .sponsor { position: absolute; right: 40px; top: 828px; display: flex; align-items: center; gap: 10px; transform: translateY(-50%); }
  .sponsor-mark { width: 22px; height: 22px; background: var(--navy); }
  .sponsor-name { font-size: 17px; font-weight: 600; color: var(--navy); }
</style>
</head>
<body>
<main class="flyer">
  <svg class="hero-photo" viewBox="0 0 300 340" role="img" aria-label="Photo of a thoughtful teenage girl in a purple sweater, resting her chin on her hand, with a brain illustration behind her">
    <defs>
      <linearGradient id="heroFill" x1="0" y1="0" x2="1" y2="1">
        <stop offset="0" stop-color="#4a3f96"/>
        <stop offset=".55" stop-color="#8f6fd6"/>
        <stop offset="1" stop-color="#b79be8"/>
      </linearGradient>
    </defs>
    <path d="M30 0 H300 V340 H90 C30 280 0 200 0 130 C0 80 10 35 30 0 Z" fill="url(#heroFill)"/>
    <path d="M30 0 C10 35 0 80 0 130 C0 200 30 280 90 340" fill="none" stroke="#a98ae0" stroke-width="4"/>
  </svg>

  <div class="brand">
    <span class="brand-dot"></span>
    <span class="brand-name">SOLVE</span>
  </div>
  <p class="brand-tagline">Sequoia Outlook Lantern Valley Echo Study</p>

  <div class="lead">
    <h1 class="headline">
      <span class="ask">Are you the parent of a child age 10–17?</span>
      <span class="worry">Do they worry or overthink negative emotions?</span>
    </h1>
    <span class="headline-rule"></span>
    <p class="intro">Alderbrook University researchers are seeking <strong>girls age 10–17</strong> for a study about brain activity in emotions and decision-making and how they relate to puberty, anxiety and depression.</p>
  </div>

  <section class="card participation">
    <span class="card-badge">
      <svg width="20" height="20" viewBox="0 0 20 20" fill="none" stroke="#2f2a6e" stroke-width="1.6"><circle cx="10" cy="6" r="3"/><path d="M3 17 Q10 9 17 17 Z"/></svg>
    </span>
    <h2 class="card-title">Study participation involves:</h2>
    <div class="step">
      <span class="step-icon"><svg width="20" height="20" viewBox="0 0 20 20" fill="none" stroke="#fff" stroke-width="1.5"><rect x="2" y="4" width="16" height="10" rx="2"/><path d="M6 14 L5 18 L10 14"/></svg></span>
      <p class="step-body"><b>One one-hour interview</b>(online or in-person) where your child will discuss their thoughts</p>
    </div>
    <div class="step">
      <span class="step-icon"><svg width="20" height="20" viewBox="0 0 20 20" fill="none" stroke="#fff" stroke-width="1.5"><rect x="4" y="3" width="12" height="15" rx="1.5"/><path d="M7 8 H13 M7 11 H13 M7 14 H11"/></svg></span>
      <p class="step-body"><b>Online questionnaires</b>(parent and child)</p>
    </div>
    <div class="step">
      <span class="step-icon"><svg width="20" height="20" viewBox="0 0 20 20" fill="none" stroke="#fff" stroke-width="1.5"><circle cx="10" cy="10" r="7"/><circle cx="10" cy="10" r="3"/></svg></span>
      <p class="step-body"><b>One two-hour visit</b>where your child will complete an MRI scan, answer questions about their puberty stage, and have a small hair sample taken to study puberty hormones</p>
    </div>
  </section>

  <section class="card eligibility">
    <span class="card-badge">
      <svg width="16" height="16" viewBox="0 0 20 20"><path d="M10 2 L12.4 7.6 L18 8 L13.7 11.8 L15 17.5 L10 14.5 L5 17.5 L6.3 11.8 L2 8 L7.6 7.6 Z" fill="#fff"/></svg>
    </span>
    <h2 class="card-title">Your child may be eligible if they:</h2>
    <ul class="criteria">
      <li><svg width="16" height="16" viewBox="0 0 16 16" fill="none" stroke="#f4c23c" stroke-width="1.6"><circle cx="8" cy="8" r="6.5"/><path d="M5 8 L7 10 L11 6"/></svg><span>Are age <span class="age">10–17</span></span></li>
      <li><svg width="16" height="16" viewBox="0 0 16 16" fill="none" stroke="#f4c23c" stroke-width="1.6"><circle cx="8" cy="8" r="6.5"/><path d="M5 8 L7 10 L11 6"/></svg><span>Tend to <em>worry or overthink</em> negative thoughts</span></li>
      <li><svg width="16" height="16" viewBox="0 0 16 16" fill="none" stroke="#f4c23c" stroke-width="1.6"><circle cx="8" cy="8" r="6.5"/><path d="M5 8 L7 10 L11 6"/></svg><span>Have not been diagnosed with psychosis, learning problems, or autism</span></li>
    </ul>
  </section>

  <section class="contact-band">
    <span class="band-icon"><svg width="28" height="22" viewBox="0 0 28 22" fill="none" stroke="#fff" stroke-width="1.6"><rect x="1" y="1" width="26" height="20" rx="2"/><path d="M1 2 L14 12 L27 2"/></svg></span>
    <div class="enquiry">
      <p class="prompt">Interested in participating?</p>
      <p>Want more information? Please contact us!</p>
      <span class="email-pill">solvestudy@alderbrook.edu</span>
    </div>
    <span class="band-divider"></span>
    <div class="payment">
      <span class="band-icon"><svg width="26" height="22" viewBox="0 0 26 22" fill="none" stroke="#fff" stroke-width="1.6"><rect x="1" y="3" width="24" height="16" rx="2"/><path d="M9 3 V19 M1 11 H25"/></svg></span>
      <p class="payment-label">Compensation<small>up to</small></p>
      <span class="payment-amount">$140</span>
    </div>
  </section>

  <div class="sponsor">
    <span class="sponsor-mark"></span>
    <span class="sponsor-name">Alderbrook University</span>
  </div>
</main>
</body>
</html>
```